Harbourline Builders Business Card Design

We need a business card for an established builder of high quality bespoke homes in Auckland and Northland. We build and renovate homes collaboratively facilitating effective communication between owners, builders, architects, suppliers and tradespeople. We have never built or renovated a home that leaks or has faults. We only use reliable materials. We have never been sued or had legal action taken against us. We are honest builders of bespoke homes not group mass produced homes. Our niche market is in character homes. We practice sustainability and have built a lot of coastal property. We have been in business for over thirty years . We would like to see natural colors of the environment sand,sea and maybe vegetation . The design should communicate quality, sustainability,fair pricing, open communication and the originality of bespoke building. And the fact that the builder is registered.

Industry/Entity Type

Business

Contact Information for Business Card

Rowan Tellick Builders
Ph. 021583917
18 Kestrel Rd Harwood Bay Auckland 0814
PO Box 927 Mangawhai 0583

```html
<!DOCTYPE html>
<html lang="en">
<head>
<meta charset="utf-8">
<title>Harbourline Builders – Business Card</title>
<link rel="stylesheet" href="https://fonts.googleapis.com/css2?family=Source+Sans+3:wght@400;600&display=swap">
<style>
  :root {
    --stage: #151515;
    --card-light: #f3f3f3;
    --brand-blue: #2b63b5;
    --brand-blue-deep: #2659a8;
    --brand-blue-soft: #3a74c4;
    --mark-grey: #9a9a9a;
    --ink: #1c1c1c;
    --white: #ffffff;
  }
  * { margin: 0; padding: 0; box-sizing: border-box; }
  html, body {
    width: 1200px;
    height: 900px;
    overflow: hidden;
  }
  body {
    background: var(--stage);
    font-family: "Source Sans 3", "Myriad Pro", sans-serif;
    position: relative;
  }
  .card {
    position: absolute;
    top: 184px;
    width: 302px;
    height: 490px;
    border-radius: 12px;
    overflow: hidden;
  }
  .card--front {
    left: 299px;
    background: var(--card-light);
    text-align: center;
    color: var(--ink);
  }
  .card--back {
    left: 646px;
    width: 303px;
    background: radial-gradient(circle at 45% 40%, var(--brand-blue-soft) 0%, var(--brand-blue) 45%, var(--brand-blue-deep) 100%);
  }
  .brand-dot {
    position: absolute;
    left: 50%;
    top: 58px;
    width: 64px;
    height: 64px;
    margin-left: -32px;
    border-radius: 50%;
    background: var(--mark-grey);
  }
  .brand-name {
    position: absolute;
    left: 0;
    right: 0;
    top: 140px;
    font-weight: 600;
    font-size: 36px;
    line-height: 38px;
    color: var(--brand-blue);
    letter-spacing: -0.5px;
  }
  .contact-name {
    position: absolute;
    left: 0;
    right: 0;
    top: 264px;
    font-weight: 600;
    font-size: 17px;
    color: var(--brand-blue);
  }
  .contact-phone {
    position: absolute;
    left: 0;
    right: 0;
    top: 321px;
    font-size: 13.5px;
    display: flex;
    justify-content: center;
    align-items: center;
    gap: 8px;
  }
  .contact-phone svg { width: 10px; height: 10px; fill: var(--brand-blue); }
  .contact-address {
    position: absolute;
    left: 0;
    right: 0;
    top: 374px;
    font-size: 13.5px;
    line-height: 20px;
    font-style: normal;
  }
  .back-name {
    position: absolute;
    right: 42px;
    top: 368px;
    text-align: right;
    font-weight: 600;
    font-size: 44px;
    line-height: 46px;
    color: var(--white);
    letter-spacing: -0.5px;
  }
</style>
</head>
<body>
  <section class="card card--front" aria-label="Card front">
    <span class="brand-dot" aria-hidden="true"></span>
    <h1 class="brand-name">Harbourline<br>Builders</h1>
    <p class="contact-name">Rowan Tellick Builders</p>
    <p class="contact-phone">
      <svg viewBox="0 0 24 24" aria-hidden="true"><path d="M6.6 10.8c1.4 2.8 3.8 5.1 6.6 6.6l2.2-2.2c.3-.3.7-.4 1-.2 1.1.4 2.3.6 3.6.6.6 0 1 .4 1 1V20c0 .6-.4 1-1 1C10.6 21 3 13.4 3 4c0-.6.4-1 1-1h3.5c.6 0 1 .4 1 1 0 1.3.2 2.5.6 3.6.1.3 0 .7-.2 1L6.6 10.8z"/></svg>
      021583917
    </p>
    <address class="contact-address">
      18 Kestrel Rd Harwood<br>
      Bay Auckland 0814<br>
      PO Box 927 Mangawhai 0583
    </address>
  </section>

  <section class="card card--back" aria-label="Card back">
    <p class="back-name">Harbourline<br>Builders</p>
  </section>
</body>
</html>
```